Redesign of business card for Cedar Ridge Mechanical

We are looking for a new design for our business cards for Cedar Ridge Mechanical. We are a plumbing & HVAC construction company, operating on the West Coast of Canada and USA. Logo attached.
Industry/Entity Type
Construction - Plumbing & HVAC
Contact Information for Business Card
Name, address, phone numbers, email, website address
Look and feel
Each slider illustrates characteristics of the customer's brand and the style your logo design should communicate.

```html
<!DOCTYPE html>
<html lang="en">
<head>
<meta charset="utf-8">
<title>Cedar Ridge Mechanical – Business Card</title>
<link rel="stylesheet" href="https://fonts.googleapis.com/css2?family=Montserrat:wght@400;700;800&display=swap">
<style>
  :root {
    --stage: #3b3b3b;
    --ink: #000000;
    --paper: #ffffff;
    --muted: #1a1a1a;
    --card-w: 520px;
    --card-h: 297px;
    --radius: 22px;
  }
  * { box-sizing: border-box; margin: 0; padding: 0; }
  html, body {
    width: 1200px;
    height: 689px;
    overflow: hidden;
    background: var(--stage);
    font-family: "Montserrat", sans-serif;
  }
  .stage {
    width: 1200px;
    height: 689px;
    display: flex;
    align-items: center;
    justify-content: center;
    gap: 60px;
  }
  .card {
    width: var(--card-w);
    height: var(--card-h);
    border-radius: var(--radius);
    position: relative;
    overflow: hidden;
  }

  /* Front */
  .card--front {
    background: var(--ink);
    display: flex;
    align-items: center;
    justify-content: center;
  }
  .brand {
    display: flex;
    align-items: center;
    gap: 14px;
    font-weight: 700;
    letter-spacing: 1px;
    text-transform: uppercase;
  }
  .brand__square {
    width: 34px;
    height: 34px;
    flex: none;
  }
  .card--front .brand { color: var(--paper); font-size: 22px; }
  .card--front .brand__square { background: var(--paper); }

  /* Back */
  .card--back {
    background: var(--paper);
    color: var(--ink);
  }
  .card--back .brand {
    position: absolute;
    left: 30px;
    top: 98px;
    width: 212px;
    font-size: 17px;
    line-height: 1.2;
    gap: 12px;
  }
  .card--back .brand__square { width: 34px; height: 34px; background: var(--ink); }
  .card--back .brand__name { display: block; }
  .divider {
    position: absolute;
    left: 262px;
    top: 62px;
    width: 1.5px;
    height: 120px;
    background: var(--ink);
  }
  .contact {
    position: absolute;
    left: 282px;
    top: 60px;
  }
  .contact__name {
    font-weight: 800;
    font-size: 21px;
    letter-spacing: 0.5px;
    text-transform: uppercase;
  }
  .contact__role {
    font-size: 13px;
    color: var(--muted);
    margin-bottom: 12px;
  }
  .contact__list { list-style: none; }
  .contact__item {
    display: flex;
    align-items: center;
    gap: 8px;
    font-size: 13.5px;
    line-height: 24px;
  }
  .contact__icon { width: 13px; height: 13px; flex: none; }
  .address-band {
    position: absolute;
    left: 0;
    right: 0;
    bottom: 18px;
    height: 32px;
    background: var(--ink);
    color: var(--paper);
    font-size: 13px;
    display: flex;
    align-items: center;
    justify-content: flex-end;
    padding-right: 130px;
  }
</style>
</head>
<body>
<main class="stage">
  <section class="card card--front">
    <div class="brand">
      <span class="brand__square"></span>
      <span class="brand__name">Cedar Ridge Mechanical</span>
    </div>
  </section>

  <section class="card card--back">
    <div class="brand">
      <span class="brand__square"></span>
      <span class="brand__name">Cedar Ridge<br>Mechanical</span>
    </div>
    <div class="divider"></div>
    <div class="contact">
      <h1 class="contact__name">Daniel Hartley</h1>
      <p class="contact__role">Managing Director</p>
      <ul class="contact__list">
        <li class="contact__item">
          <svg class="contact__icon" viewBox="0 0 24 24" aria-hidden="true"><path fill="currentColor" d="M6.6 10.8a15 15 0 0 0 6.6 6.6l2.2-2.2c.3-.3.7-.4 1-.2 1.1.4 2.3.6 3.6.6.6 0 1 .4 1 1V20c0 .6-.4 1-1 1A17 17 0 0 1 3 4c0-.6.4-1 1-1h3.5c.6 0 1 .4 1 1 0 1.3.2 2.5.6 3.6.1.3 0 .7-.2 1z"/></svg>
          123 456 789
        </li>
        <li class="contact__item">
          <svg class="contact__icon" viewBox="0 0 24 24" aria-hidden="true"><path fill="currentColor" d="M3 5h18v14H3zm2 2v.5l7 4.5 7-4.5V7zm0 2.9V17h14V9.9l-7 4.5z"/></svg>
          info@yourgmail.com
        </li>
        <li class="contact__item">
          <svg class="contact__icon" viewBox="0 0 24 24" aria-hidden="true"><circle cx="12" cy="12" r="9" fill="none" stroke="currentColor" stroke-width="2"/><path d="M3 12h18M12 3c3 3 3 15 0 18M12 3c-3 3-3 15 0 18" fill="none" stroke="currentColor" stroke-width="1.6"/></svg>
          www.yourwebsite.com
        </li>
      </ul>
    </div>
    <div class="address-band">Your address, City State, Zip 1234</div>
  </section>
</main>
</body>
</html>
```